Brookvale Estates LLC stationary for a real estate property management company.

Create stationary (letterhead, envelopes, business cards) using Brookvale Estates LLC logo as primary creative element. Stationary design needs to be horizontal, leaving as much space as possible for correspondence copy. See attached Creative Brief and past stationary files for details.

Target Market(s)

Prospective apartment residents and current residents, vendors, and government agencies.

Industry/Entity Type

Property Management

Contact Information for Business Card

Business card employee title: Property Manager. Should include address, phone, fax, email, website, slogan, and Brookvale Estates logo.

Font styles to use
Sans Serif

Colors
0592cd
000000

Requirements
Must have
• Tone should be conservative, institutional, business (i.e. banking, finance, real estate). Must include: address, phone, fax, website, and slogan (see attached Creative Brief). Should be a horizontal design, leaving as much room as possible for letter correspondence copy.
Nice to have
• Please use an Arial or Helvetica style font.
Should not have
• Letterhead layout should leave as much room as possible for copy.

```html
<!DOCTYPE html>
<html lang="en">
<head>
<meta charset="utf-8">
<title>Brookvale Estates LLC – Stationery</title>
<link href="https://fonts.googleapis.com/css2?family=Arimo:wght@400;700&display=swap" rel="stylesheet">
<style>
  :root{
    --brand:#1b72ae;
    --ink:#2a2a2a;
    --muted:#555;
    --paper:#ffffff;
    --backdrop:#ececec;
    --edge:#dcdcdc;
  }
  *{box-sizing:border-box;margin:0;padding:0}
  html,body{width:1200px;height:938px;overflow:hidden}
  body{background:var(--backdrop);font-family:"Arimo",Arial,sans-serif;color:var(--ink);position:relative}
  .sheet{position:absolute;background:var(--paper);border:1px solid var(--edge)}
  .wordmark{display:flex;align-items:center;gap:5px;color:var(--brand);font-weight:700;line-height:1}
  .wordmark .mark{background:var(--brand);flex:none}
  .wordmark .name{display:flex;flex-direction:column}
  .wordmark .sub{letter-spacing:.14em}
  .web{position:absolute;left:0;right:0;text-align:center;letter-spacing:.32em;color:var(--ink)}

  /* letterhead */
  .letterhead{left:184px;top:68px;width:387px;height:544px}
  .letterhead .wordmark{position:absolute;left:20px;top:34px}
  .letterhead .mark{width:14px;height:14px}
  .letterhead .main{font-size:17px}
  .letterhead .sub{font-size:7px;margin-top:2px}
  .contact{position:absolute;left:316px;top:24px;list-style:none;font-size:4.4px;line-height:8px;color:var(--muted)}
  .contact li{display:flex;align-items:center;gap:3px}
  .contact i{width:4px;height:4px;border-radius:50%;background:var(--brand);display:inline-block}
  .letter{position:absolute;left:38px;top:137px;width:300px;font-size:5.4px;line-height:8.4px;color:var(--ink)}
  .letter p{margin-bottom:8px}
  .letter .gap{margin-bottom:24px}
  .letter b{font-weight:700}
  .signature{width:38px;height:22px;background:linear-gradient(90deg,#e9e9e9,#f5f5f5);margin:6px 0 8px}
  .letterhead .web{top:512px;font-size:8.6px}

  /* folder */
  .folder{left:637px;top:42px;width:458px;height:574px}
  .folder .wordmark{position:absolute;left:80px;top:246px;gap:12px}
  .folder .mark{width:44px;height:52px}
  .folder .main{font-size:38px}
  .folder .sub{font-size:16px;margin-top:4px;letter-spacing:.16em}
  .folder .web{top:541px;font-size:9.6px}

  /* business cards */
  .card{width:177px;height:98px;border-radius:8px}
  .card-front{left:46px;top:660px}
  .card-front .wordmark{position:absolute;right:10px;top:10px;gap:3px}
  .card-front .mark{width:9px;height:12px}
  .card-front .main{font-size:11.5px}
  .card-front .sub{font-size:4.6px;margin-top:1px}
  .card-front .slogan{position:absolute;right:10px;top:30px;font-size:4px;color:var(--muted);letter-spacing:.04em}
  .card-front .address{position:absolute;left:9px;top:40px;font-size:3.6px;line-height:5px;color:var(--ink)}
  .card-front .contact{left:9px;top:53px;font-size:3.2px;line-height:5.6px}
  .card-front .contact i{width:3px;height:3px}
  .card-front .person{position:absolute;right:10px;top:82px;text-align:right;font-size:4px;line-height:5px}
  .card-front .person b{color:var(--brand);font-weight:400;font-size:4.6px}
  .card-back{left:46px;top:786px;height:99px}
  .card-back .wordmark{position:absolute;left:46px;top:38px;gap:3px}
  .card-back .mark{width:10px;height:14px}
  .card-back .main{font-size:13px}
  .card-back .sub{font-size:5.2px;margin-top:1px}

  /* envelopes */
  .envelope{left:266px;top:674px;width:430px;height:207px}
  .envelope .wordmark{position:absolute;left:16px;top:28px;gap:5px}
  .envelope .mark{width:14px;height:18px}
  .envelope .main{font-size:17px}
  .envelope .sub{font-size:7px;margin-top:2px}
  .envelope .web{top:180px;font-size:8.6px}
  .envelope-back{left:737px;top:674px;width:432px;height:206px}
  .envelope-back .flap{position:absolute;left:0;top:0;width:100%;height:70px;background:var(--brand);border-radius:0 0 38px 38px}
  .envelope-back .web{top:28px;color:#fff;font-size:10.6px}
</style>
</head>
<body>

<section class="sheet letterhead">
  <div class="wordmark"><span class="mark"></span><span class="name"><span class="main">BROOKVALE</span><span class="sub">ESTATES LLC</span></span></div>
  <ul class="contact">
    <li><i></i>012 555 0148</li>
    <li><i></i>012 555 0148</li>
    <li><i></i>012 555 0148</li>
    <li><i></i>info@brookvaleestates.com</li>
    <li><i></i>www.brookvaleestates.com</li>
  </ul>
  <div class="letter">
    <p>July 2, 2012</p>
    <p><b>Dear CH,</b><br>Harbor Building, Elm St., Country Name</p>
    <p>is simply dummy text of the printing and typesetting industry. Lorem Ipsum has been the industry's standard<br>dummy text ever since the 1500s, when an unknown printer took a galley of type and scrambled it to make<br>a type specimen book. It has survived not only five centuries, but also the leap into electronic typesetting,<br>remaining essentially unchanged. It was popularised in the 1960s with the release of Letraset sheets containing<br>Lorem Ipsum passages, and more recently with desktop publishing software like Aldus PageMaker including<br>versions of Lorem Ipsum.</p>
    <p class="gap">is simply dummy text of the printing and typesetting industry. Lorem Ipsum has been the industry's standard<br>dummy text ever since the 1500s, when an unknown printer took a galley of type and scrambled it to make</p>
    <p>is simply dummy text of the printing and typesetting industry. Lorem Ipsum has been the industry's standard<br>dummy text ever since the 1500s, when an unknown printer took a galley of type and scrambled it to make<br>a type specimen book. It has survived not only five centuries, but also the leap into electronic typesetting,<br>remaining essentially unchanged. It was popularised in the 1960s with the release of Letraset sheets containing<br>Lorem Ipsum passages, and more recently with desktop publishing software like Aldus PageMaker including<br>versions of Lorem Ipsum.</p>
    <p style="margin-bottom:0">Best Regards,</p>
    <div class="signature" role="img" aria-label="Handwritten signature"></div>
    <p><b>Daniel Reyes</b><br>Director</p>
    <p>Harbor Building, Elm St., Country Name</p>
  </div>
  <div class="web">www.brookvaleestates.com</div>
</section>

<section class="sheet folder">
  <div class="wordmark"><span class="mark"></span><span class="name"><span class="main">BROOKVALE</span><span class="sub">ESTATES LLC</span></span></div>
  <div class="web">www.brookvaleestates.com</div>
</section>

<section class="sheet card card-front">
  <div class="wordmark"><span class="mark"></span><span class="name"><span class="main">BROOKVALE</span><span class="sub">ESTATES LLC</span></span></div>
  <div class="slogan">Managing homes with care</div>
  <div class="address">210 Oak Road<br>3rd Floor, Suite 4</div>
  <ul class="contact">
    <li><i></i>Phone 012 555 0148</li>
    <li><i></i>Mobile 012 555 0147</li>
    <li><i></i>Fax 012 555 0149</li>
    <li><i></i>info@brookvaleestates.com</li>
    <li><i></i>www.brookvaleestates.com</li>
  </ul>
  <div class="person"><b>MARK ELLISON</b><br>PROPERTY MANAGER</div>
</section>

<section class="sheet card card-back">
  <div class="wordmark"><span class="mark"></span><span class="name"><span class="main">BROOKVALE</span><span class="sub">ESTATES LLC</span></span></div>
</section>

<section class="sheet envelope">
  <div class="wordmark"><span class="mark"></span><span class="name"><span class="main">BROOKVALE</span><span class="sub">ESTATES LLC</span></span></div>
  <div class="web">www.brookvaleestates.com</div>
</section>

<section class="sheet envelope-back">
  <div class="flap"></div>
  <div class="web">www.brookvaleestates.com</div>
</section>

</body>
</html>
```